Flaschenetiketten-Design in rechteckiger Grundform für Biermanufaktur
Zielgruppe
Wir repräsentieren eine Bier-Manufaktur in der Gründungsphase und sind auf der Suche nach einem Designvorschlag für die Flaschenetiketten.
Unsere Zielgruppe sind Liebhaber, die auf der Suche nach dem Speziellen und Lokalen sind. Der Biergenuss abseits des Massenmarktes soll im Entwurf sichtbar/transportiert werden. Die Bier-Manufaktur steht zeitgleich für Trend-Kreationen mit bodenständigem Ursprung.
Aufgabenstellung
Die Herkunft der Gründer Familie aus dem Schweizer Kanton Simplon soll im Vordergrund stehen, hierzu bitte das Familienwappen / einzelne Elemente siehe Dateiupload berücksichtigen.
Das Etikett soll eine rechteckige Grundform haben.
Folgende Angaben sollen sich im Etikett wiederfinden:
- Biersorte: 'Lager' (zukünftig soll es möglich sein, Biersorte auf dem Etikett zu wechseln)
Brand: 'Hearty Kandrom'
'Biermanufaktur Walliser Ursprungs'
Die Schrift soll klar und nicht zu verspielt sein.

```html
<!DOCTYPE html>
<html lang="de">
<head>
<meta charset="utf-8">
<title>Hearty Kandrom – Lagerbier Etikett</title>
<link rel="stylesheet" href="https://fonts.googleapis.com/css2?family=Montserrat:wght@500;600&display=swap">
<style>
  :root {
    --page: #ffffff;
    --frame: #5b5c5e;
    --band: #4f5052;
    --band-line: #3a3b3d;
    --band-text: #c9cacc;
    --night: #2b3944;
    --stone: #4a473f;
    --lower: #2e3033;
    --white: #ffffff;
  }
  * { margin: 0; padding: 0; box-sizing: border-box; }
  html, body { width: 844px; height: 1200px; overflow: hidden; background: var(--page); }
  body { position: relative; font-family: "Montserrat", sans-serif; }

  .label {
    position: absolute; left: 213px; top: 64px; width: 401px; height: 444px;
    background: var(--frame);
    box-shadow: 8px 12px 18px rgba(0,0,0,.35);
  }
  .label__photo {
    position: absolute; left: 7px; top: 7px; width: 387px; height: 305px;
    background: radial-gradient(ellipse at 40% 75%, #6a6454 0%, var(--stone) 35%, var(--night) 82%),
                var(--night);
  }
  .label__title {
    position: absolute; left: 0; right: 0; top: 112px;
    color: var(--white); text-align: center; font-weight: 600;
    font-size: 56px; line-height: 56px; letter-spacing: 3px;
  }
  .label__band {
    position: absolute; left: 7px; top: 314px; width: 387px; height: 46px;
    background: var(--band);
    border-top: 1px solid var(--band-line); border-bottom: 1px solid var(--band-line);
  }
  .label__band-text {
    position: absolute; top: 15px; color: var(--band-text);
    font-size: 10px; font-weight: 600; letter-spacing: 1.5px; line-height: 14px;
  }
  .label__band-text--left { left: 13px; }
  .label__band-text--right { right: 2px; }
  .label__lower {
    position: absolute; left: 7px; top: 362px; width: 387px; height: 75px;
    background: linear-gradient(90deg, #36373a, var(--lower) 60%, #26282b);
  }
  .label__mark {
    position: absolute; left: 163px; top: 306px; width: 75px; height: 75px;
    background: var(--band); border: 2px solid var(--band-text);
  }
  .label__variety {
    position: absolute; left: 0; right: 0; top: 400px; text-align: center;
    color: var(--white); font-size: 15px; font-weight: 600; letter-spacing: 2.4px;
  }

  .neck {
    position: absolute; left: 392px; top: 620px; width: 60px; height: 270px;
  }
  .neck__head {
    position: absolute; left: 0; top: 0; width: 60px; height: 60px;
    background: var(--band); border: 2px solid var(--band-text);
  }
  .neck__strip {
    position: absolute; left: 14px; top: 58px; width: 32px; height: 200px;
    background: var(--band); border: 1px solid var(--band-line); border-top: none;
    border-radius: 0 0 16px 16px;
  }
  .neck__variety {
    position: absolute; left: 50%; top: 50%;
    transform: translate(-50%, -50%) rotate(-90deg);
    color: var(--band-text); font-size: 14px; font-weight: 600; letter-spacing: 2px;
    white-space: nowrap;
  }
</style>
</head>
<body>
  <section class="label">
    <div class="label__photo" role="img" aria-label="Foto: alter Steinbau vor verschneiten Bergen in der Dämmerung"></div>
    <h1 class="label__title">HEARTY<br>KANDROM</h1>
    <div class="label__band">
      <span class="label__band-text label__band-text--left">BIERMANUFAKTUR</span>
      <span class="label__band-text label__band-text--right">WALLISER URSPRUNGS</span>
    </div>
    <div class="label__lower"></div>
    <div class="label__mark"></div>
    <p class="label__variety">- LAGERBIER -</p>
  </section>

  <section class="neck">
    <div class="neck__strip"><span class="neck__variety">LAGERBIER</span></div>
    <div class="neck__head"></div>
  </section>
</body>
</html>
```